Brenwick Structures Construction Company Seeking Modern Website

We are a small construction company wanting to create a web presence. We don't have much in the way of current content but will get photos as they come in. Attached is a picture of our business card.
The pages we would like on the menu are:
Home
Portfolio
Product Specs
Testimonials
Our Process
Contact
Some designs we like are:
http://www.tovasheds-example.com/
http://www.qrnstructures-example.com/
http://dunholtbarns-example.com/
http://pellingframes-example.com/
Not much requirements other than that so feel free to be creative!
Updates
Target Market(s)
Construction
Commercial and Residential Buildings
Industry/Entity Type
Construction Company
Number of Pages Required
5+ page
Look and feel

```html
<!DOCTYPE html>
<html lang="en">
<head>
<meta charset="utf-8">
<title>Brenwick Structures</title>
<link href="https://fonts.googleapis.com/css2?family=Oswald:wght@300;400&family=Roboto:wght@300;400;500;700&display=swap" rel="stylesheet">
<style>
:root{
  --red:#dc2b1f;
  --blue:#139fdc;
  --dark:#2b2b2b;
  --charcoal:#444546;
  --grey-bg:#ebeeef;
  --text:#555;
  --muted:#9a9a9a;
  --line:#dcdcdc;
  --white:#fff;
}
*{box-sizing:border-box;margin:0;padding:0}
html,body{width:1200px;height:3046px;overflow:hidden}
body{font-family:'Roboto',Arial,sans-serif;color:var(--text);background:var(--white)}
a{color:inherit;text-decoration:none}

/* header */
.site-header{height:145px;position:relative;border-bottom:1px solid var(--line)}
.call{position:absolute;left:98px;top:62px;display:flex;align-items:center;gap:14px}
.call-icon{width:50px;height:50px;border-radius:50%;border:2px solid #d9d9d9;display:flex;align-items:center;justify-content:center}
.call small{display:block;font-size:12px;color:#888}
.call strong{font-size:18px;font-weight:500;color:#333}
.brand{position:absolute;left:0;right:0;top:50px;text-align:center;font-size:36px;font-weight:700;color:var(--red)}
.search{position:absolute;left:870px;top:66px;width:232px;height:40px;border:1px solid #ccc;display:flex}
.search span{flex:1;font-size:12px;color:#aaa;padding:12px 10px}
.search .go{width:54px;background:var(--blue);clip-path:polygon(28% 0,100% 0,100% 100%,0 100%,0 0);display:flex;align-items:center;justify-content:flex-end;padding-right:12px}

/* nav */
.main-nav{height:65px;display:flex;border-bottom:1px solid var(--line)}
.main-nav a{font-size:12px;font-weight:500;color:#444;text-transform:uppercase;display:flex;align-items:center;justify-content:center;border-right:1px solid var(--line);position:relative}
.main-nav a:last-child{border-right:0}
.nav-home{width:230px;padding-left:90px;color:var(--red)!important;border-right:0!important}
.nav-home svg{position:absolute;left:100px;top:18px}
.nav-home::after{content:"";position:absolute;left:100px;right:0;bottom:-1px;height:4px;background:var(--red)}
.nav-home::before{content:"";position:absolute;left:153px;bottom:3px;width:10px;height:10px;border-radius:50%;background:var(--red)}
.main-nav a.n{width:178px}
.main-nav a.n-wide{width:200px}

/* hero */
.hero{height:563px;position:relative;background:linear-gradient(180deg,#3c4a5d 0%,#6f7f8f 35%,#4d6040 70%,#2f4a22 100%);overflow:hidden}
.hero-shade{position:absolute;left:320px;top:290px;width:560px;height:273px;background:linear-gradient(180deg,rgba(0,0,0,.0),rgba(0,0,0,.3))}
.hero-title{position:absolute;left:0;right:0;top:318px;text-align:center;font-family:'Oswald',sans-serif}
.hero-title h1{font-weight:400;font-size:58px;color:var(--blue);line-height:1.1}
.hero-title p{font-weight:300;font-size:52px;color:var(--white);line-height:1.25}
.hero-arrow{position:absolute;top:262px;width:44px;height:44px;border-radius:50%;border:2px solid rgba(255,255,255,.75);display:flex;align-items:center;justify-content:center}
.hero-arrow.prev{left:51px}.hero-arrow.next{left:1103px}

/* welcome */
.welcome{height:285px;text-align:center;padding-top:40px}
.section-title{display:inline-block;font-size:25px;font-weight:500;color:var(--red);text-transform:uppercase;padding:0 30px 14px;border-bottom:2px solid #e4e4e4;border-radius:0 0 50% 50%}
.section-title span{color:var(--blue)}
.welcome p{width:880px;margin:26px auto 0;font-size:12px;line-height:22px;color:#777;font-weight:300}
.btn-dark{display:inline-block;margin-top:30px;width:104px;height:40px;line-height:40px;background:var(--charcoal);color:var(--white);font-size:11px;font-weight:700;text-transform:uppercase}

/* services */
.services{height:760px;background:var(--grey-bg);padding:51px 98px 0}
.services-panel{background:var(--white);height:648px;position:relative}
.tabs{height:64px;display:flex;position:relative;background:var(--charcoal)}
.tab{font-size:20px;text-transform:uppercase;color:var(--white);display:flex;align-items:center;justify-content:center}
.tab.active{width:500px;background:var(--red);clip-path:polygon(0 0,450px 0,500px 100%,0 100%);padding-right:50px;justify-content:flex-start;padding-left:130px}
.tab.other{flex:1;padding-right:60px}
.tab-pointer{position:absolute;left:165px;top:64px;border:18px solid transparent;border-top:18px solid var(--red);border-bottom:0}
.service-list{position:absolute;left:38px;top:120px;list-style:none;width:410px}
.service-list li{height:63px;font-size:22px;color:#444;display:flex;align-items:center;padding-left:10px;text-transform:uppercase}
.service-list li.current{color:var(--red);background:#e9edef;clip-path:polygon(0 0,382px 0,410px 50%,382px 100%,0 100%)}
.service-feature{position:absolute;left:500px;top:92px;width:494px;border:1px solid #ddd;padding:5px 5px 0}
.feature-photo{height:285px;background:linear-gradient(180deg,#6f82b5 0%,#a0a8c9 40%,#7a6a5c 75%,#3d3a3f 100%)}
.feature-body{height:237px;margin:2px -6px 0;background:var(--blue);color:var(--white);text-align:center;padding-top:26px}
.feature-body h3{font-size:17px;font-weight:500;text-transform:uppercase}
.feature-body p{font-size:12px;line-height:21px;width:400px;margin:14px auto 0;font-weight:300}
.feature-actions{display:flex;justify-content:center;gap:54px;margin-top:22px}
.feature-actions a{height:40px;width:126px;display:flex;align-items:center;justify-content:center;gap:6px;font-size:11px;font-weight:700;text-transform:uppercase}
.btn-red{background:var(--red)}
.btn-grey{background:var(--charcoal)}

/* testimonial */
.testimonial{height:367px;text-align:center;padding-top:38px;position:relative}
.quote-rule{position:absolute;top:66px;height:1px;background:#ccc;width:330px}
.quote-rule.l{left:240px}.quote-rule.r{right:240px}
.quote-mark{font-family:'Oswald',sans-serif;font-size:96px;line-height:60px;color:var(--red);height:50px;overflow:hidden}
.testimonial blockquote{margin-top:22px;font-size:21px;line-height:35px;color:#333}
.author{display:inline-block;margin-top:12px;font-size:15px;font-weight:500;color:var(--blue);position:relative;padding:0 90px}
.author::before,.author::after{content:"";position:absolute;top:9px;width:180px;height:1px;background:#ddd}
.author::before{right:100%;margin-right:-90px}.author::after{left:100%;margin-left:-90px}
.dots{display:flex;justify-content:center;gap:16px;margin-top:26px}
.dots i{width:13px;height:13px;border-radius:50%;background:#ccc}
.dots i.on{background:var(--blue)}

/* blog */
.blog{height:507px;background:var(--grey-bg);text-align:center;padding-top:45px}
.blog-grid{display:flex;margin:30px 0 0 100px;text-align:left}
.post{width:290px}
.post + .post{margin-left:65px;position:relative}
.post + .post::before{content:"";position:absolute;left:-32px;top:0;height:300px;width:1px;background:#d4d4d4}
.post-photo{height:200px;border:4px solid var(--white)}
.p1{background:linear-gradient(160deg,#5a3f6e,#a0794a 60%,#3a2a22)}
.p2{background:linear-gradient(180deg,#6e8fc0,#c7ccd5 50%,#6d7a58)}
.p3{background:linear-gradient(180deg,#3b8bd6,#9cc3e0 45%,#4a7c4a)}
.post-meta{display:flex;gap:18px;margin-top:27px}
.date{width:60px;height:70px;background:var(--red);color:var(--white);text-align:center;flex:none}
.date small{display:block;font-size:11px;padding-top:8px}
.date b{font-size:28px;font-weight:400}
.post h4{font-size:13px;font-weight:500;color:#333;margin-top:-2px}
.post p{font-size:11px;line-height:18px;color:var(--muted);margin-top:8px}

/* footer */
.site-footer{height:354px;background:var(--dark);color:#ddd;position:relative}
.f-col{position:absolute;top:52px}
.f-col h5{font-size:14px;font-weight:500;color:var(--white);text-transform:uppercase;margin-bottom:26px}
.f-col li{list-style:none;font-size:12px;line-height:21px}
.f-col.featured li::before{content:"› ";color:var(--red)}
.f-sep{position:absolute;top:52px;width:1px;height:150px;background:#444}
.newsletter p{font-size:12px;color:#999;margin-top:-14px}
.newsletter .field{width:238px;height:34px;background:#eee;margin-top:16px;font-size:11px;color:#999;padding:10px}
.newsletter .btn-red{display:inline-block;margin:12px 0 0 140px;width:98px;height:32px;line-height:32px;text-align:center;font-size:13px;font-weight:700;color:var(--white)}
.social{position:absolute;left:0;right:0;top:248px;display:flex;justify-content:center;gap:14px}
.social span{width:42px;height:42px;border:2px solid var(--red);display:block}
.copyright{position:absolute;left:0;right:0;top:314px;text-align:center;font-size:11px;color:#aaa}
</style>
</head>
<body>

<header class="site-header">
  <div class="call">
    <div class="call-icon">
      <svg width="24" height="24" viewBox="0 0 24 24"><path d="M6.6 10.8c1.4 2.8 3.8 5.1 6.6 6.6l2.2-2.2c.3-.3.7-.4 1-.2 1.1.4 2.3.6 3.6.6.6 0 1 .4 1 1V20c0 .6-.4 1-1 1C10.6 21 3 13.4 3 4c0-.6.4-1 1-1h3.5c.6 0 1 .4 1 1 0 1.3.2 2.5.6 3.6.1.3 0 .7-.2 1z" fill="var(--blue)"/></svg>
    </div>
    <div><small>Call Us Today!</small><strong>260.555.0147</strong></div>
  </div>
  <div class="brand">Brenwick Structures</div>
  <div class="search"><span>Search...</span><div class="go">
    <svg width="16" height="16" viewBox="0 0 16 16"><circle cx="6.5" cy="6.5" r="4.5" fill="none" stroke="#fff" stroke-width="2"/><path d="M10 10l4 4" stroke="#fff" stroke-width="2.2"/></svg>
  </div></div>
</header>

<nav class="main-nav">
  <a class="nav-home" href="#">
    <svg width="26" height="22" viewBox="0 0 26 22"><path d="M13 1L1 11h3v10h7v-6h4v6h7V11h3z" fill="var(--red)"/></svg>Home</a>
  <a class="n" href="#">Portfolio</a>
  <a class="n-wide" href="#" style="width:200px">Product Specs</a>
  <a class="n" href="#" style="width:195px">Testimonials</a>
  <a class="n" href="#" style="width:180px">Our Process</a>
  <a class="n" href="#" style="width:215px">Contact</a>
</nav>

<section class="hero" role="img" aria-label="Photo of a large two-storey house with bay windows on a green lawn">
  <div class="hero-shade"></div>
  <a class="hero-arrow prev" href="#"><svg width="12" height="16" viewBox="0 0 12 16"><path d="M9 2L3 8l6 6" fill="none" stroke="#fff" stroke-width="2"/></svg></a>
  <a class="hero-arrow next" href="#"><svg width="12" height="16" viewBox="0 0 12 16"><path d="M3 2l6 6-6 6" fill="none" stroke="#fff" stroke-width="2"/></svg></a>
  <div class="hero-title">
    <h1>BUILDING DREAMS</h1>
    <p>So You Can Build Memories</p>
  </div>
</section>

<section class="welcome">
  <h2 class="section-title">Welcome to <span>Brenwick Structures</span></h2>
  <p>There are many variations of passages of Lorem Ipsum available, but the majority have suffered alteration in some form, by injected humour, or randomised words which don't look even slightly believable. If you are going to use a passage of Lorem Ipsum, you need to be sure there isn't anything embarrassing hidden in the middle of text. of text. All the Lorem Ipsum generators on the Internet tend to repeat predefined chunks as necessary.</p>
  <a class="btn-dark" href="#">More Info</a>
</section>

<section class="services">
  <div class="services-panel">
    <div class="tabs">
      <div class="tab active">Commercial</div>
      <div class="tab other">Residential</div>
    </div>
    <span class="tab-pointer"></span>
    <ul class="service-list">
      <li class="current">Design Build</li>
      <li>Farm &amp; Agriculture</li>
      <li>Equestrian</li>
      <li>Commercial</li>
      <li>Community</li>
      <li>Design Build</li>
      <li>Equestrian</li>
      <li>Community</li>
    </ul>
    <div class="service-feature">
      <div class="feature-photo" role="img" aria-label="Photo of a modern glass office building lit at dusk"></div>
      <div class="feature-body">
        <h3>Commercial Construction</h3>
        <p>There are many variations of passages of Lorem Ipsum available, but the majority have suffered alteration in some form, by injected humour, andomised words which don't look even slightly believable.</p>
        <div class="feature-actions">
          <a class="btn-red" href="#">Read More
            <svg width="11" height="11" viewBox="0 0 11 11"><rect x=".5" y=".5" width="10" height="10" fill="none" stroke="#fff"/><path d="M5.5 2.5v6M2.5 5.5h6" stroke="#fff"/></svg></a>
          <a class="btn-grey" href="#">Quick View
            <svg width="14" height="10" viewBox="0 0 14 10"><path d="M1 5c2-4 10-4 12 0-2 4-10 4-12 0z" fill="#fff"/><circle cx="7" cy="5" r="2" fill="var(--charcoal)"/></svg></a>
        </div>
      </div>
    </div>
  </div>
</section>

<section class="testimonial">
  <span class="quote-rule l"></span><span class="quote-rule r"></span>
  <div class="quote-mark">&ldquo;</div>
  <blockquote>My Varlen C Series failed the nct on emmisions. I have been using some&nbsp; fuel<br>treatments from KVM for about 3 weeks and the car passed the nct,<br>majority have suffered alteration in some form</blockquote>
  <div class="author">DANORWELL</div>
  <div class="dots"><i></i><i class="on"></i><i></i></div>
</section>

<section class="blog">
  <h2 class="section-title">Our <span style="color:var(--red)">Blog</span></h2>
  <div class="blog-grid">
    <article class="post">
      <div class="post-photo p1" role="img" aria-label="Photo of a warmly lit restaurant interior"></div>
      <div class="post-meta"><div class="date"><small>Oct</small><b>04</b></div>
        <div><h4>Designing the Best Pole Barn</h4><p>Eastbrook College's Shared and Core Facilities Office is responsible for helping to manage hundreds of important pieces of</p></div></div>
    </article>
    <article class="post">
      <div class="post-photo p2" role="img" aria-label="Photo of a suburban two-storey family home"></div>
      <div class="post-meta"><div class="date"><small>Oct</small><b>05</b></div>
        <div><h4>Making Your Pole Barn Unique</h4><p>Eastbrook College's Shared and Core Facilities Office is responsible for helping to manage hundreds of important pieces of</p></div></div>
    </article>
    <article class="post">
      <div class="post-photo p3" role="img" aria-label="Photo of city towers beside palm trees"></div>
      <div class="post-meta"><div class="date"><small>Oct</small><b>06</b></div>
        <div><h4>Does Your Barn Need a Detention</h4><p>Eastbrook College's Shared and Core Facilities Office is responsible for helping to manage hundreds of important pieces of</p></div></div>
    </article>
  </div>
</section>

<footer class="site-footer">
  <div class="f-col" style="left:99px"><h5>Services</h5>
    <ul><li>Commercial,</li><li>Residential</li><li>Farm &amp; Agriculture</li><li>Equestrian</li><li>Design Build</li></ul></div>
  <span class="f-sep" style="left:270px"></span>
  <div class="f-col featured" style="left:343px"><h5>Featured Services</h5>
    <ul><li>Available Property</li><li>Property Showcase</li><li>Commercial Services</li><li>Work Order</li></ul></div>
  <span class="f-sep" style="left:540px"></span>
  <div class="f-col newsletter" style="left:604px"><h5>Sign to Newsletter</h5>
    <p>Join our confidential network and be the</p>
    <div class="field">Enter Your Email</div>
    <a class="btn-red" href="#">Subscribe</a></div>
  <span class="f-sep" style="left:902px"></span>
  <div class="f-col" style="left:970px"><h5>Contact Us</h5>
    <ul><li>2280 W. 41st Tr. Street</li><li>Fairhollow, KS 66000</li><li>Call : (91) 555-0142</li><li>Fax : (91) 555-0143</li></ul></div>
  <div class="social" aria-label="Social links"><span></span><span></span><span></span><span></span></div>
  <div class="copyright">Copyright ©2015 Brenwick Structures all Right Reserved</div>
</footer>

</body>
</html>
```